Qvx Brightforge Website

All the descriptions are available in the attached file. The designer has to structure the website and find the right images and icons. The website should look modern and avoid using images of real humans rather use animated images. Please note that the design should include home page, all the 4 services page , the contact us would be at the bottom of home page.

```html
<!DOCTYPE html>
<html lang="en">
<head>
<meta charset="utf-8">
<title>Qvx Brightforge</title>
<link href="https://fonts.googleapis.com/css2?family=Orbitron:wght@500;600&family=Nunito:wght@400;600;700;800&display=swap" rel="stylesheet">
<style>
:root{
  --blue:#1a6fe0;
  --blue-deep:#0f68dc;
  --pale:#eef4fd;
  --pale-2:#e4eefc;
  --ink:#1b1b1b;
  --text:#3d3d3d;
  --orange:#ff9b00;
  --line:#d9e3f0;
  --white:#fff;
}
*{box-sizing:border-box;margin:0;padding:0}
html,body{width:1200px;height:3637px;overflow:hidden;background:var(--white)}
body{position:relative;font-family:"Nunito",sans-serif;color:var(--text)}
.abs{position:absolute}
.display{font-family:"Orbitron",sans-serif;color:var(--ink);font-weight:500}
.brand{font-family:"Nunito",sans-serif;font-weight:800;color:var(--blue);font-size:25px;line-height:1.05}
.nav{top:32px;left:611px;display:flex;gap:22px;align-items:center;font-size:14px;font-weight:700;color:#222;letter-spacing:.3px}
.nav .active{background:var(--blue);color:#fff;border-radius:16px;padding:6px 15px}
.hero-text{left:133px;top:208px;font-size:22px;line-height:37px;letter-spacing:.5px;width:320px}
.section-title{left:0;width:1200px;text-align:center;font-size:24px;letter-spacing:1px}
.divider{left:572px;width:56px;height:12px}
.card{background:#fff;border-radius:26px;box-shadow:0 6px 26px rgba(30,80,160,.09);width:452px;height:213px}
.card .icon{position:absolute;left:32px;top:41px;width:113px;height:121px;border-radius:26px;background:var(--pale)}
.card h3{position:absolute;left:190px;top:34px;font-size:16px;font-family:"Orbitron",sans-serif;font-weight:500;color:var(--ink)}
.card p{position:absolute;left:190px;top:70px;width:245px;font-size:12px;line-height:16px;color:#333}
.btn{display:inline-block;background:var(--orange);color:#fff;font-weight:800;font-size:11px;border-radius:14px;padding:6px 14px;letter-spacing:.3px}
.card .btn{position:absolute;left:190px;top:154px}
.welcome p{font-size:13.5px;line-height:20.8px;text-align:justify;color:#333}
.blog{width:452px;height:529px;border:1px solid var(--line);border-radius:30px;background:#fff}
.blog .art{position:absolute;left:40px;top:14px;width:372px;height:233px;border-radius:18px}
.blog h3{position:absolute;left:45px;top:276px;width:370px;font-family:"Orbitron",sans-serif;font-weight:500;font-size:16px;line-height:29px;color:var(--ink)}
.blog p{position:absolute;left:45px;top:350px;width:358px;font-size:13px;line-height:19px;text-align:justify;color:#333}
.blog .btn{position:absolute;left:45px;top:476px}
.field{border:1px solid var(--line);background:#fff;border-radius:22px;font-size:12px;color:#444;padding:13px 20px}
.footer{color:#fff}
.footer h4{font-size:13px;font-weight:800;letter-spacing:.3px;padding-bottom:6px;border-bottom:2px solid #fff}
.footer .item{font-size:12px;line-height:16px;display:flex;gap:10px;align-items:flex-start}
.footer .dot{width:22px;height:22px;border-radius:50%;background:#fff;flex:none;display:flex;align-items:center;justify-content:center}
.menu-list{font-size:12px;line-height:19px}
</style>
</head>
<body>

<!-- hero backdrop -->
<svg class="abs" style="left:0;top:0" width="1200" height="700" aria-hidden="true">
  <path d="M0 0 H560 C590 80 640 130 700 180 C760 240 720 330 640 420 C560 520 420 650 260 660 C150 665 60 630 0 610 Z" fill="var(--pale)"/>
</svg>

<div class="abs brand" style="left:134px;top:34px">Qvx<br>Brightforge</div>

<nav class="abs nav">
  <span class="active">HOME</span><span>SERVICES</span><span>PRODUCTS</span><span>BLOG</span><span>CONTACT US</span>
</nav>

<h1 class="abs display hero-text">EMPOWER YOUR DIGITAL JOURNEY WITH OUR ADVANCED IT SOLUTIONS. FROM DATA TO WEB AND MOBILE APPS, WE'VE GOT YOU COVERED.</h1>

<div class="abs" role="img" aria-label="Isometric illustration of a laptop with a developer, CMS badge, cloud upload, gears, security shield and browser windows" style="left:470px;top:141px;width:600px;height:450px;border-radius:48% 40% 44% 50%;background:linear-gradient(135deg,#cfe0fb,#8fb3f0 60%,#3b73da)"></div>

<!-- services -->
<h2 class="abs display section-title" style="top:684px">OUR SERVICES</h2>
<svg class="abs divider" style="top:739px" viewBox="0 0 56 12" aria-hidden="true"><line x1="6" y1="6" x2="50" y2="6" stroke="var(--blue)" stroke-width="2"/><circle cx="6" cy="6" r="4" fill="#fff" stroke="var(--blue)" stroke-width="2"/><circle cx="50" cy="6" r="4" fill="#fff" stroke="var(--blue)" stroke-width="2"/></svg>

<div class="abs card" style="left:133px;top:798px">
  <div class="icon" role="img" aria-label="Data analytics icon"></div>
  <h3>Data Analytics</h3>
  <p>At Qvx Brightforge, our proficiency consists of linking your leadership team's objectives with the relevant data that holds significance.</p>
  <span class="btn">READ MORE</span>
</div>
<div class="abs card" style="left:616px;top:798px">
  <div class="icon" role="img" aria-label="Web development icon"></div>
  <h3>Web Development</h3>
  <p>At Qvx Brightforge, we are a trailblazing web development company committed tod elivering cutting-edge digital solutions that empower businesses</p>
  <span class="btn">READ MORE</span>
</div>
<div class="abs card" style="left:133px;top:1038px">
  <div class="icon" role="img" aria-label="Mobile app development icon"></div>
  <h3>Mobile App Development</h3>
  <p>At Qvx Brightforge, we are a pioneering mobile app development company dedicated to crafting exceptional digital experiences that captivate</p>
  <span class="btn">READ MORE</span>
</div>
<div class="abs card" style="left:616px;top:1038px">
  <div class="icon" role="img" aria-label="Start-up rocket icon"></div>
  <h3>Start-up Partner</h3>
  <p>At Qvx Brightforge, we are committed to supporting early-stage start-ups on their journey to success by providing comprehensive technical partner services.</p>
  <span class="btn">READ MORE</span>
</div>

<!-- welcome -->
<svg class="abs" style="left:0;top:1320px" width="1200" height="640" aria-hidden="true">
  <path d="M0 60 C120 10 300 20 420 90 C560 170 620 320 560 450 C500 560 320 640 140 620 C80 612 30 600 0 590 Z" fill="var(--pale)"/>
  <path d="M1200 560 C1140 520 1060 600 1100 660 L1200 660 Z" fill="var(--pale)"/>
</svg>
<div class="abs" role="img" aria-label="Illustration of a team working with dashboards, charts and a large gear" style="left:141px;top:1363px;width:466px;height:494px;border-radius:24px;background:linear-gradient(160deg,#dbe5fb,#8ea8e8 55%,#f3b53f)"></div>

<div class="abs welcome" style="left:682px;top:1362px;width:377px">
  <h2 class="display" style="font-size:24px;line-height:36px;letter-spacing:1px">WELCOME TO<br>QVX BRIGHTFORGE</h2>
  <svg style="display:block;margin-top:20px" width="56" height="12" viewBox="0 0 56 12" aria-hidden="true"><line x1="6" y1="6" x2="50" y2="6" stroke="var(--blue)" stroke-width="2"/><circle cx="6" cy="6" r="4" fill="#fff" stroke="var(--blue)" stroke-width="2"/><circle cx="50" cy="6" r="4" fill="#fff" stroke="var(--blue)" stroke-width="2"/></svg>
  <p style="margin-top:36px">We are a forward-thinking IT consulting firm specializing in providing cutting-edge data analytics, web application development, and mobile app development services. Our passion for innovation and technology drives us to deliver tailor-made solutions that empower businesses to thrive in the digital landscape.</p>
  <p style="margin-top:26px">We take pride in our ability to collaborate with early-stage startups as their technology partner, helping them navigate the challenges of launching and scaling their ventures. Our team of experienced professionals works closely with clients, understanding their unique requirements and goals, to craft bespoke solutions that propel growth and foster success.</p>
  <span class="btn" style="margin-top:38px">READ MORE</span>
</div>

<!-- blog -->
<h2 class="abs display section-title" style="top:1983px">LATEST BLOG</h2>
<svg class="abs divider" style="top:2037px" viewBox="0 0 56 12" aria-hidden="true"><line x1="6" y1="6" x2="50" y2="6" stroke="var(--blue)" stroke-width="2"/><circle cx="6" cy="6" r="4" fill="#fff" stroke="var(--blue)" stroke-width="2"/><circle cx="50" cy="6" r="4" fill="#fff" stroke="var(--blue)" stroke-width="2"/></svg>

<div class="abs blog" style="left:134px;top:2104px">
  <div class="art" role="img" aria-label="Illustration of people presenting charts on a large folding board with gears" style="background:linear-gradient(150deg,#eaf2fb,#3f92e3 60%,#1b5fb8)"></div>
  <h3>Lorem ipsum dolor sit ametconsect etur adipiscing elit, sed dood</h3>
  <p>Sed ut perspiciatis unde omnis iste natus error sit voluptatem accusantium doloremque laudantium, totam rem aperiam, eaque ipsa quae ab illo inventore veritatis et quasi architecto beatae vitae dicta sunt explicabo. Nemo enim ipsam voluptatem</p>
  <span class="btn">READ MORE</span>
</div>
<div class="abs blog" style="left:617px;top:2104px">
  <div class="art" role="img" aria-label="Illustration of a person beside a growing bar and line chart" style="background:linear-gradient(150deg,#f5f5fb,#c9c5f3 60%,#6a5fd8)"></div>
  <h3>Lorem ipsum dolor sit ametconsect etur adipiscing elit, sed dood</h3>
  <p>Sed ut perspiciatis unde omnis iste natus error sit voluptatem accusantium doloremque laudantium, totam rem aperiam, eaque ipsa quae ab illo inventore veritatis et quasi architecto beatae vitae dicta sunt explicabo. Nemo enim ipsam voluptatem</p>
  <span class="btn">READ MORE</span>
</div>

<!-- contact -->
<svg class="abs" style="left:0;top:2700px" width="1200" height="937" aria-hidden="true">
  <path d="M0 30 C300 0 600 60 900 40 C1030 30 1130 20 1200 10 V937 H0 Z" fill="var(--pale)"/>
  <path d="M0 535 C220 600 460 590 700 560 C920 530 1080 500 1200 540 V937 H0 Z" fill="var(--blue-deep)"/>
</svg>

<h2 class="abs display section-title" style="top:2791px">CONTACT US</h2>
<svg class="abs divider" style="top:2846px" viewBox="0 0 56 12" aria-hidden="true"><line x1="6" y1="6" x2="50" y2="6" stroke="var(--blue)" stroke-width="2"/><circle cx="6" cy="6" r="4" fill="#fff" stroke="var(--blue)" stroke-width="2"/><circle cx="50" cy="6" r="4" fill="#fff" stroke="var(--blue)" stroke-width="2"/></svg>

<div class="abs field" style="left:241px;top:2897px;width:232px;height:42px">Name</div>
<div class="abs field" style="left:484px;top:2897px;width:232px;height:42px">Email</div>
<div class="abs field" style="left:726px;top:2897px;width:233px;height:42px">Phone Number</div>
<div class="abs field" style="left:241px;top:2952px;width:716px;height:150px;border-radius:18px">Message</div>
<span class="abs btn" style="left:553px;top:3137px;width:94px;height:33px;text-align:center;font-size:12px;padding-top:9px;border-radius:16px">SUBMIT</span>

<!-- footer -->
<footer class="footer">
  <div class="abs brand" style="left:137px;top:3352px;color:#fff;font-size:34px">Qvx<br>Brightforge</div>

  <div class="abs" style="left:400px;top:3318px;width:193px">
    <h4>CONTACT US</h4>
    <div class="item" style="margin-top:22px"><span class="dot"><svg width="10" height="12" viewBox="0 0 10 12"><path d="M5 0a4 4 0 0 1 4 4c0 3-4 8-4 8S1 7 1 4a4 4 0 0 1 4-4z" fill="var(--blue)"/></svg></span><span>Suite 12/40 Harbourline Road, Eastvale WA 6190</span></div>
    <div class="item" style="margin-top:18px"><span class="dot"><svg width="11" height="11" viewBox="0 0 12 12"><path d="M2 1l3 2-1 2a7 7 0 0 0 3 3l2-1 2 3-2 1C5 11 1 7 1 3z" fill="var(--blue)"/></svg></span><span>Call Us<br>+61 (08) 5550 2741</span></div>
    <div class="item" style="margin-top:18px"><span class="dot"><svg width="11" height="8" viewBox="0 0 11 8"><rect width="11" height="8" rx="1" fill="var(--blue)"/><path d="M0 0l5.5 4L11 0" stroke="#fff" fill="none"/></svg></span><span>E mail Us<br>dev@qvxbrightforge.example</span></div>
  </div>

  <div class="abs" style="left:710px;top:3318px;width:108px">
    <h4>MENU</h4>
    <div class="menu-list" style="margin-top:18px">Home<br>Services<br>Products<br>Blog<br>Contact us</div>
  </div>

  <div class="abs" style="left:959px;top:3318px;width:106px">
    <h4>FOLLOW US</h4>
    <div class="item" style="margin-top:22px"><span class="dot"></span><span>Like us on<br>FRIENDSPACE</span></div>
    <div class="item" style="margin-top:18px"><span class="dot"></span><span>Follow us on<br>CHIRPER</span></div>
    <div class="item" style="margin-top:18px"><span class="dot"></span><span>Follow us on<br>PROLINK</span></div>
  </div>

  <div class="abs" style="left:127px;top:3555px;width:935px;height:1px;background:rgba(255,255,255,.7)"></div>
  <div class="abs" style="left:0;top:3593px;width:1200px;text-align:center;font-size:11px">Copyright © 2023 All Rights Reserved</div>
</footer>

</body>
</html>
```